QRN Roasting Company - design for coffee company logo and 12 oz coffee bags

I would like to start selling coffee and need both a brand logo as well as packaging design for the coffee bags. The name of the company is QRN Roasting Company. I have a related brand for a youtube channel called QRNBX4T, I will attach that logo to the uploaded files. The branding for the coffee should compliment QRNBX4T, but doesn't have to (and probably should NOT be too close in similarity). The Company Brand logo should be featured on the bag, but not as dominant/large as the specific product label (like Tailwind 4700).
This coffee will be marketed towards aviation consumers. Pilots, dispatchers, ATC professionals, mechanics, etc. Male dominated market. Masculine themes needed.
For the bag design, I need one standard bag design to use across all my products, then I will simply add the SKU product names to all the interchangeable bags. So my design request is for a dark bag with airspace lines/designs/graphics in a repeatable format that I can cast to the printing design. I am adding inspiration upload for this. I'm thinking using a light or white color for the shapes/vectors/symbols on the dark bag. Not all of the different shapes and icons should be included, but things like the compass circle with tick marks, line vectors stretching out in different directions. Again - don't need ALL of the shapes and text. certainly not the green stuff. And important to note, the inspiration uploads I've provided have white background and darker lines/shapes. I would like to inverse that for this design. Dark bag and light shapes/lines.
If you could include the first product label for the bag, that would be great. The first coffee product will be called "Tailwind 4700". I've included an example I tried to make on Figma, but I'm an awful designer. The example I included has the "1200" on an aviation transponder. This is the code plugged into the airplane that lets ATC know who you are and where you are. In the final delivery, I would like the product label (Tailwind 4700) to be separate from the bag itself so I can change it out with other coffee product labels for my light and dark roasts. A section at the bottom with roast profile, grind type, source, etc should be located on the bottom (or wherever it makes sense). The inspiration for the layout could come from the lower section of the Approach Plate i attached.
On the back, a section that notes details about the company:
"QRN Roasting Company was built for people who start the day with somewhere to go — pilots, builders, travelers, early risers, and anyone chasing the next leg of the journey.
QRN is a nod to our home skies under Palmer Ridge Sector and to Zero Fuel Weight — the aviation reminder that every mission starts with what you choose to carry.
Brew Your Climb."

Where the package opens at the top, a horizontal image that says "REMOVE BEFORE FLIGHT" is a nice to have. Inspiration image uploaded to the brief. This is a standard cover on aircraft to protect sensitive instruments/equipment. Located right where the folded seal of the bag is would be a nice touch. Red with white text.

Target Market(s)

aviation professionals and enthusiasts... who like coffee. Pilots, dispatchers, military, Air Traffic Control, Mechanics. Mostly male crowd.

Industry/Entity Type

Coffee company, but aviation style branding

Requirements
Nice to have
• company tagline "Brew Your Climb" - experiment with placing - either under company logo - on sides/back - whatever looks/feels right.
Should not have
• do not include the uploaded QRN BX4T logo on the package. It's for reference as a sister brand only.

```html
<!DOCTYPE html>
<html lang="en">
<head>
<meta charset="utf-8">
<title>QRN Roasting Company – Tailwind 4700 Bag</title>
<link href="https://fonts.googleapis.com/css2?family=Barlow:wght@400;500;600&family=Barlow+Semi+Condensed:wght@500;600;700&family=Orbitron:wght@600&display=swap" rel="stylesheet">
<style>
  :root {
    --page: #ffffff;
    --bag: #161616;
    --bag-light: #242424;
    --ink: #e4e0d8;
    --ink-soft: #b9b5ad;
    --rule: #8d8a84;
    --band: #b8322c;
    --band-dark: #9a2822;
    --band-text: #f6f1ea;
    --display: #0a0d10;
    --digit: #f4f6f8;
  }
  * { box-sizing: border-box; margin: 0; padding: 0; }
  html, body { width: 1200px; height: 1200px; overflow: hidden; background: var(--page); }
  .canvas { position: relative; width: 1200px; height: 1200px; }

  .bag {
    position: absolute; top: 210px; height: 788px;
    background: var(--bag); border-radius: 14px; overflow: hidden;
    color: var(--ink); font-family: "Barlow Semi Condensed", sans-serif;
  }
  .bag--front { left: 122px; width: 472px; }
  .bag--back { left: 634px; width: 453px; }

  .chart-pattern {
    position: absolute; inset: 0;
    background: radial-gradient(ellipse at 50% 52%, var(--bag-light) 0%, var(--bag) 70%);
  }

  .flight-band {
    position: absolute; left: 0; right: 0; top: 32px; height: 31px;
    background: linear-gradient(var(--band), var(--band-dark));
    border-top: 1px dashed rgba(255,255,255,.25);
    border-bottom: 1px dashed rgba(255,255,255,.25);
    display: flex; align-items: center; justify-content: center; gap: 14px;
    color: var(--band-text); font-weight: 700; font-size: 19px; letter-spacing: 1.2px;
  }
  .flight-band svg { width: 70px; height: 20px; }

  .brand { position: absolute; left: 0; right: 0; text-align: center; }
  .brand__name { font-weight: 700; font-size: 36px; letter-spacing: 2px; line-height: 1; color: var(--ink); }
  .brand__sub { font-weight: 700; font-size: 9px; letter-spacing: 2px; margin-top: 6px; color: var(--ink); }
  .brand__star { display: block; margin: 8px auto 0; width: 14px; height: 14px; }
  .bag--front .brand { top: 198px; }
  .bag--back .brand { top: 210px; }
  .bag--back .brand__name { font-size: 40px; }
  .bag--back .brand__sub { font-size: 10px; }

  .transponder {
    position: absolute; left: 98px; top: 349px; width: 278px; height: 191px;
    background: #1c1d1f; border: 1px solid #3a3b3d; border-radius: 10px;
    box-shadow: 0 6px 14px rgba(0,0,0,.6);
    text-align: center;
  }
  .screw { position: absolute; width: 13px; height: 13px; border-radius: 50%; background: #3b3b3b; border: 1px solid #555; }
  .screw--tl { left: 9px; top: 9px; } .screw--tr { right: 9px; top: 9px; }
  .screw--bl { left: 9px; bottom: 9px; } .screw--br { right: 9px; bottom: 9px; }
  .transponder__title { margin-top: 24px; font-weight: 700; font-size: 23px; letter-spacing: 4px; color: var(--ink); }
  .transponder__display {
    margin: 8px auto 0; width: 236px; height: 82px; background: var(--display);
    border: 1px solid #2c2f33; border-radius: 3px;
    display: flex; align-items: center; justify-content: center;
    font-family: "Orbitron", sans-serif; font-weight: 600; font-size: 58px; letter-spacing: 6px;
    color: var(--digit); text-shadow: 0 0 8px rgba(255,255,255,.55);
  }
  .transponder__blend { margin-top: 10px; font-weight: 600; font-size: 17px; letter-spacing: 4px; color: var(--ink); }

  .spec-table {
    position: absolute; left: 39px; top: 618px; width: 397px; height: 108px;
    border: 1px solid var(--rule); font-weight: 600; font-size: 11.5px; letter-spacing: .8px; line-height: 1.55;
  }
  .spec-row { position: absolute; left: 0; right: 0; height: 54px; display: flex; }
  .spec-row--top { top: 0; border-bottom: 1px solid var(--rule); }
  .spec-row--bottom { top: 54px; }
  .spec-cell { display: flex; align-items: center; gap: 12px; padding-left: 15px; border-right: 1px solid var(--rule); height: 100%; }
  .spec-cell:last-child { border-right: none; }
  .spec-icon { width: 56px; padding: 0; justify-content: center; }
  .spec-icon svg, .spec-cell svg { width: 24px; height: 24px; flex: none; }

  .net-weight { position: absolute; left: 0; right: 0; top: 746px; text-align: center; font-weight: 500; font-size: 13px; letter-spacing: 2.5px; }

  .story {
    position: absolute; left: 110px; top: 318px; width: 250px; white-space: nowrap;
    font-family: "Barlow", sans-serif; font-weight: 400; font-size: 12.3px; line-height: 19.7px; letter-spacing: .4px; color: var(--ink);
  }
  .story p + p { margin-top: 18px; }
  .story__tagline { margin-top: 22px; font-family: "Barlow Semi Condensed", sans-serif; font-weight: 700; font-size: 18px; letter-spacing: 1.6px; line-height: 1; }

  .back-ornament { position: absolute; left: 0; right: 0; top: 594px; display: flex; justify-content: center; }
  .back-ornament svg { width: 100px; height: 24px; }

  .back-table {
    position: absolute; left: 38px; top: 650px; width: 376px; height: 52px;
    border: 1px solid var(--rule); display: flex;
    font-weight: 600; font-size: 9.5px; letter-spacing: 1px; line-height: 1.75;
  }
  .back-table .spec-cell { padding-left: 14px; gap: 12px; white-space: nowrap; }
  .back-table .spec-cell:nth-child(1) { width: 119px; }
  .back-table .spec-cell:nth-child(2) { width: 138px; }
  .back-table .spec-cell:nth-child(3) { flex: 1; }
  .back-table svg { width: 20px; height: 20px; }

  .site { position: absolute; left: 0; right: 0; top: 724px; text-align: center; font-weight: 500; font-size: 12px; letter-spacing: 3px; }
  .socials { position: absolute; left: 0; right: 0; top: 753px; display: flex; justify-content: center; gap: 18px; }
  .socials span { width: 15px; height: 15px; border: 1.5px solid var(--ink-soft); border-radius: 50%; }
</style>
</head>
<body>
<div class="canvas">

  <section class="bag bag--front">
    <div class="chart-pattern" role="img" aria-label="Light airspace chart lines, radials and compass rose with tick marks on a dark ground"></div>

    <div class="flight-band">
      <span>REMOVE BEFORE FLIGHT</span>
      <svg viewBox="0 0 70 20" aria-hidden="true"><line x1="0" y1="10" x2="44" y2="10" stroke="currentColor" stroke-width="1.5"/><path d="M44 9h22l3 1-3 1H44zM54 10l-6-9h3l9 9-9 9h-3zM46 10l-3-4h2l3 4-3 4h-2z" fill="currentColor"/></svg>
    </div>

    <div class="brand">
      <div class="brand__name">QRN</div>
      <div class="brand__sub">ROASTING COMPANY</div>
    </div>

    <div class="transponder">
      <span class="screw screw--tl"></span><span class="screw screw--tr"></span>
      <span class="screw screw--bl"></span><span class="screw screw--br"></span>
      <div class="transponder__title">TAILWIND</div>
      <div class="transponder__display">4700</div>
      <div class="transponder__blend">VFR BLEND</div>
    </div>

    <div class="spec-table">
      <div class="spec-row spec-row--top">
        <div class="spec-cell spec-icon"><svg viewBox="0 0 24 24"><ellipse cx="12" cy="12" rx="7" ry="10" transform="rotate(25 12 12)" fill="var(--ink)"/><path d="M15 4c-5 5 0 11-6 16" stroke="var(--bag)" stroke-width="1.6" fill="none"/></svg></div>
        <div class="spec-cell" style="width:108px">ROAST<br>MEDIUM</div>
        <div class="spec-cell" style="width:137px"><svg viewBox="0 0 24 24" fill="none" stroke="var(--ink)" stroke-width="1.3"><circle cx="12" cy="12" r="10"/><ellipse cx="12" cy="12" rx="4.5" ry="10"/><path d="M2 12h20M4 7h16M4 17h16"/></svg><span>ORIGIN<br>COLOMBIA</span></div>
        <div class="spec-cell" style="flex:1">ALTITUDE<br>1800m</div>
      </div>
      <div class="spec-row spec-row--bottom">
        <div class="spec-cell spec-icon"><svg viewBox="0 0 24 24" fill="none" stroke="var(--ink)" stroke-width="1.4"><path d="M1 20l7-12 4 6 3-4 8 10z"/></svg></div>
        <div class="spec-cell" style="width:206px">NOTES<br>CHOCOLATE · CITRUS · ALMOND</div>
        <div class="spec-cell" style="flex:1"><svg viewBox="0 0 24 24" fill="var(--ink)"><circle cx="12" cy="6" r="4.5"/><circle cx="6" cy="17" r="4.5"/><circle cx="18" cy="17" r="4.5"/></svg><span>GRIND<br>WHOLE BEAN</span></div>
      </div>
    </div>

    <div class="net-weight">NET WT. 12OZ (340G)</div>
  </section>

  <section class="bag bag--back">
    <div class="chart-pattern" role="img" aria-label="Light airspace chart lines and route vectors on a dark ground"></div>

    <div class="flight-band" style="top:34px">
      <span>REMOVE BEFORE FLIGHT</span>
      <svg viewBox="0 0 70 20" aria-hidden="true"><line x1="0" y1="10" x2="44" y2="10" stroke="currentColor" stroke-width="1.5"/><path d="M44 9h22l3 1-3 1H44zM54 10l-6-9h3l9 9-9 9h-3zM46 10l-3-4h2l3 4-3 4h-2z" fill="currentColor"/></svg>
    </div>

    <div class="brand">
      <div class="brand__name">QRN</div>
      <div class="brand__sub">ROASTING COMPANY</div>
      <svg class="brand__star" viewBox="0 0 24 24" aria-hidden="true"><path d="M12 1l3.2 7.2 7.8.7-5.9 5.2 1.8 7.7L12 17.8 5.1 21.8l1.8-7.7L1 8.9l7.8-.7z" fill="var(--ink-soft)"/></svg>
    </div>

    <div class="story">
      <p>QRN Roasting Company was built for<br>people who start the day with<br>somewhere to go — pilots, builders,<br>travelers, early risers, and anyone<br>chasing the next leg of the journey.</p>
      <p>QRN is a nod to our home skies<br>under Palmer Ridge Sector and to<br>Zero Fuel Weight — the aviation<br>reminder that every mission starts<br>with what you choose to carry.</p>
      <div class="story__tagline">BREW YOUR CLIMB.</div>
    </div>

    <div class="back-ornament" aria-hidden="true">
      <svg viewBox="0 0 100 24"><path d="M50 1l3 7h7.5l-6 4.5 2.3 7.5L50 15.5 43.2 20l2.3-7.5-6-4.5H47z" fill="var(--ink-soft)"/><path d="M2 9h34M8 13h28M14 17h22M64 9h34M64 13h28M64 17h22" stroke="var(--ink-soft)" stroke-width="1.3"/></svg>
    </div>

    <div class="back-table">
      <div class="spec-cell"><svg viewBox="0 0 24 24" fill="var(--ink-soft)"><path d="M12 2c1 5 7 8 7 14a7 7 0 0 1-14 0c0-4 3-5 3-9 2 2 3 3 3 5 1-3 1-6 1-10z"/></svg><span>ROASTED ON<br>05.15.25</span></div>
      <div class="spec-cell"><svg viewBox="0 0 24 24" fill="none" stroke="var(--ink-soft)" stroke-width="1.4"><circle cx="12" cy="12" r="8"/><path d="M12 1v6M12 17v6M1 12h6M17 12h6"/></svg><span>BATCH NO.<br>QRN-051525</span></div>
      <div class="spec-cell"><svg viewBox="0 0 24 24" fill="var(--ink-soft)"><path d="M11 2h2v8l9 4v2l-9-2v5l3 2v1l-4-1-4 1v-1l3-2v-5l-9 2v-2l9-4z"/></svg><span>FUEL UP.<br>FLY SAFE.</span></div>
    </div>

    <div class="site">QRNROASTING.COM</div>
    <div class="socials" aria-label="Social channels"><span></span><span></span><span></span></div>
  </section>

</div>
</body>
</html>
```